Coastline Premier Retreats Business Card Design

Design a business card for Coastline Premier Retreats. Look at the website for colors and reference. Card should have logo, name, title, office number, mobile number, email, URL and a tagline like, "Luxury Hotel & Resort Email Marketing" (This might change).

https://www.coastlinepremierretreats.example

The rest I will leave up to your imagination.

Contact Information for Business Card

Logo, name, title, office number, mobile number, email, URL and a tagline like, "Luxury Hotel & Resort Email Marketing" (This might change).

```html
<!DOCTYPE html>
<html lang="en">
<head>
<meta charset="utf-8">
<title>Coastline Premier Retreats – Business Card</title>
<link rel="stylesheet" href="https://fonts.googleapis.com/css2?family=Montserrat:wght@400;500;700;800&display=swap">
<style>
  :root {
    --backdrop: #262626;
    --card: #181818;
    --orange: #f07d1a;
    --white: #f4f4f4;
    --faint: #3a3a3a;
  }
  * { box-sizing: border-box; margin: 0; padding: 0; }
  html, body { width: 1200px; height: 1200px; overflow: hidden; }
  body {
    background: var(--backdrop);
    font-family: "Montserrat", sans-serif;
    position: relative;
  }
  .card {
    position: absolute;
    top: 250px;
    width: 400px;
    height: 700px;
    background: var(--card);
    border-radius: 28px;
    box-shadow: 0 18px 40px rgba(0,0,0,0.45);
    overflow: hidden;
  }
  .card--front { left: 150px; }
  .card--back { left: 650px; }

  .brand {
    position: absolute;
    writing-mode: vertical-rl;
    transform: rotate(180deg);
    font-weight: 700;
    text-transform: uppercase;
    letter-spacing: 2px;
    line-height: 1.15;
  }
  .card--front .brand {
    left: 48px;
    top: 40px;
    font-size: 27px;
    color: var(--white);
  }
  .brand-square {
    position: absolute;
    width: 18px;
    height: 18px;
    background: var(--orange);
  }
  .card--front .brand-square { left: 62px; top: 380px; }

  .person {
    position: absolute;
    left: 44px;
    right: 36px;
    bottom: 46px;
  }
  .person__name {
    font-weight: 800;
    font-size: 34px;
    color: var(--orange);
    letter-spacing: 1px;
    line-height: 1;
  }
  .person__title {
    font-size: 19px;
    color: var(--white);
    margin-top: 4px;
    line-height: 1.2;
  }
  .rule { height: 2px; background: var(--orange); margin: 12px 0; }
  .address { font-size: 15px; color: var(--white); line-height: 1.4; }
  .contacts { list-style: none; }
  .contacts li {
    display: flex;
    align-items: center;
    gap: 8px;
    font-size: 14px;
    color: var(--white);
    line-height: 1.6;
    white-space: nowrap;
  }
  .contacts svg { width: 13px; height: 13px; flex: none; }
  .contacts .accent { color: var(--orange); }

  .card--back .brand {
    left: 150px;
    top: 110px;
    font-size: 42px;
    color: var(--faint);
  }
  .card--back .brand-square { left: 170px; top: 625px; background: var(--faint); width: 22px; height: 22px; }
  .tagline {
    position: absolute;
    right: 46px;
    top: 90px;
    writing-mode: vertical-rl;
    transform: rotate(180deg);
    font-size: 21px;
    font-weight: 400;
    color: var(--orange);
    letter-spacing: 0.5px;
  }
</style>
</head>
<body>
  <section class="card card--front" aria-label="Business card front">
    <div class="brand">Coastline<br>Premier Retreats</div>
    <span class="brand-square"></span>

    <div class="person">
      <h1 class="person__name">MARCUS HALE</h1>
      <p class="person__title">CEO/Founder</p>
      <div class="rule"></div>
      <p class="address">Po Box, 77 B Shore Rd<br>Seaview Bay, CA 30915</p>
      <div class="rule"></div>
      <ul class="contacts">
        <li>
          <svg viewBox="0 0 12 12"><rect x="3" y="0.5" width="6" height="11" rx="1.2" fill="none" stroke="#f07d1a" stroke-width="1.2"/><circle cx="6" cy="9.5" r="0.7" fill="#f07d1a"/></svg>
          555.204.1870
        </li>
        <li>
          <svg viewBox="0 0 12 12"><path d="M1 4 Q6 0 11 4 L10 5.5 L8 5 L7.5 3.8 Q6 3.4 4.5 3.8 L4 5 L2 5.5 Z" fill="#f07d1a"/><rect x="2.5" y="6" width="7" height="5" rx="1" fill="#f07d1a"/></svg>
          +34 611 482 739
        </li>
        <li>
          <svg viewBox="0 0 12 12"><rect x="0.5" y="2.5" width="11" height="7.5" fill="#f07d1a"/><path d="M0.5 2.5 L6 7 L11.5 2.5" fill="none" stroke="#181818" stroke-width="1"/></svg>
          info@coastlinepremierretreats.example
        </li>
        <li>
          <svg viewBox="0 0 12 12"><circle cx="6" cy="6" r="5.3" fill="#f07d1a"/><path d="M3 4 Q5 3 5 5.5 Q4 7 5.5 9" fill="none" stroke="#181818" stroke-width="1"/><path d="M8 2.5 Q7 5 9 6.5" fill="none" stroke="#181818" stroke-width="1"/></svg>
          <span>www.<span class="accent">coastlinepremierretreats</span>.example</span>
        </li>
      </ul>
    </div>
  </section>

  <section class="card card--back" aria-label="Business card back">
    <div class="brand">Coastline<br>Premier Retreats</div>
    <span class="brand-square"></span>
    <p class="tagline">Luxury Hotel &amp; Resort Email Marketing</p>
  </section>
</body>
</html>
```